Trading Company needs a business card design, letter head design and email signature

We need a double-sided business card design, letter head design and an email signature. We have a logo design.

Possible Tag Lines:
• “Connecting Worlds, Building Excellence.”
• “Global Sourcing, Local Excellence.”
• “Bridging Borders, Building Quality.”
• “Worldwide Partnerships, Superior Goods.”
• “Where Quality Meets Affordability”

Services Offered:
Procurement
Fabrication
Distribution
Logistics
Import/Export

Requirements
Must have
• Nice quality double sided Business Card design, Letterhead design needs to be A4
Nice to have
• possible ideas on tag lines

```html
<!DOCTYPE html>
<html lang="en">
<head>
<meta charset="utf-8">
<title>Tradevane Business Card</title>
<link href="https://fonts.googleapis.com/css2?family=Open+Sans:wght@400;600;700&display=swap" rel="stylesheet">
<style>
  :root {
    --red: #e41f26;
    --grey: #55585a;
    --ink: #1d1d1f;
    --paper: #ffffff;
    --backdrop: #ece8e4;
  }
  * { box-sizing: border-box; margin: 0; padding: 0; }
  html, body { width: 1200px; height: 780px; overflow: hidden; }
  body {
    background: var(--backdrop);
    font-family: "Open Sans", Arial, sans-serif;
    color: var(--ink);
    display: flex;
    align-items: center;
    justify-content: center;
    gap: 40px;
  }
  .card {
    width: 560px;
    height: 320px;
    background: var(--paper);
    position: relative;
    box-shadow: 0 6px 18px rgba(0,0,0,0.18);
    overflow: hidden;
  }

  /* brand lockup */
  .brand {
    display: flex;
    align-items: center;
    gap: 10px;
    position: absolute;
  }
  .brand-square {
    width: 26px;
    height: 26px;
    background: var(--red);
  }
  .brand-name {
    font-weight: 700;
    font-size: 34px;
    letter-spacing: 2px;
    color: var(--grey);
    line-height: 1;
  }

  /* front */
  .front .brand { top: 38px; right: 56px; }
  .person { position: absolute; left: 40px; top: 108px; }
  .person-name {
    font-size: 30px;
    font-weight: 700;
    color: var(--red);
    line-height: 1.1;
  }
  .person-name .surname { color: var(--grey); }
  .person-title {
    font-size: 15px;
    font-weight: 600;
    color: var(--ink);
    margin-top: 4px;
  }
  .divider {
    position: absolute;
    left: 300px;
    top: 112px;
    width: 1px;
    height: 110px;
    background: var(--red);
  }
  .contacts {
    position: absolute;
    left: 322px;
    top: 122px;
    list-style: none;
  }
  .contacts li {
    display: flex;
    align-items: center;
    gap: 9px;
    font-size: 15px;
    line-height: 1.65;
    color: var(--ink);
  }
  .contacts svg { width: 14px; height: 14px; flex: none; }
  .services-label {
    position: absolute;
    left: 40px;
    bottom: 56px;
    font-size: 14px;
    font-weight: 700;
    letter-spacing: 0.5px;
    color: var(--red);
  }
  .services-band {
    position: absolute;
    left: 0;
    right: 0;
    bottom: 22px;
    height: 30px;
    background: var(--red);
    display: flex;
    align-items: center;
    padding-left: 34px;
    gap: 12px;
    list-style: none;
  }
  .services-band li {
    color: var(--paper);
    font-size: 14px;
    display: flex;
    align-items: center;
    gap: 7px;
  }
  .services-band li::before {
    content: "";
    width: 7px;
    height: 7px;
    background: var(--paper);
    transform: rotate(45deg);
  }

  /* back */
  .back .brand { top: 96px; left: 50%; transform: translateX(-50%); }
  .back .brand-square { width: 34px; height: 34px; }
  .back .brand-name { font-size: 44px; }
  .taglines {
    position: absolute;
    left: 30px;
    right: 30px;
    top: 176px;
    text-align: center;
    font-size: 12.5px;
    line-height: 1.9;
    color: var(--ink);
  }
  .tagline {
    display: inline-flex;
    align-items: center;
    gap: 6px;
    margin: 0 5px;
    white-space: nowrap;
  }
  .tagline::before {
    content: "";
    width: 7px;
    height: 7px;
    background: var(--red);
    transform: rotate(45deg);
  }
</style>
</head>
<body>

  <section class="card front" aria-label="Business card front">
    <div class="brand">
      <span class="brand-square"></span>
      <span class="brand-name">TRADEVANE</span>
    </div>

    <div class="person">
      <p class="person-name">Lukas <span class="surname">Veren</span></p>
      <p class="person-title">Managing Director</p>
    </div>

    <span class="divider"></span>

    <ul class="contacts">
      <li>
        <svg viewBox="0 0 16 16" aria-hidden="true"><path fill="#e41f26" d="M3.6 1.2l2.2 2.6-1.3 1.6c.9 2 2.5 3.6 4.6 4.6l1.6-1.3 2.6 2.2-1.5 2.3C6.5 13 3 9.5 1.2 4.2z"/></svg>
        (555) 014-2290
      </li>
      <li>
        <svg viewBox="0 0 16 16" aria-hidden="true"><rect x="1" y="3" width="14" height="10" fill="#e41f26"/><path d="M1.5 3.5L8 9l6.5-5.5" fill="none" stroke="#fff" stroke-width="1.3"/></svg>
        info@tradevane.example
      </li>
      <li>
        <svg viewBox="0 0 16 16" aria-hidden="true"><circle cx="8" cy="8" r="7" fill="#e41f26"/><path d="M1 8h14M8 1c-3 3.5-3 10.5 0 14M8 1c3 3.5 3 10.5 0 14" fill="none" stroke="#fff" stroke-width="1"/></svg>
        www.tradevane.example
      </li>
    </ul>

    <p class="services-label">SERVICES</p>
    <ul class="services-band">
      <li>Procurement</li>
      <li>Fabrication</li>
      <li>Distribution</li>
      <li>Logistics</li>
      <li>Import/Export</li>
    </ul>
  </section>

  <section class="card back" aria-label="Business card back">
    <div class="brand">
      <span class="brand-square"></span>
      <span class="brand-name">TRADEVANE</span>
    </div>

    <div class="taglines">
      <span class="tagline">Connecting Worlds, Building Excellence</span>
      <span class="tagline">Global Sourcing, Local Excellence</span><br>
      <span class="tagline">Bridging Borders, Building Quality</span>
      <span class="tagline">Worldwide Partnerships, Superior Goods</span><br>
      <span class="tagline">Where Quality Meets Affordability</span>
    </div>
  </section>

</body>
</html>
```